Keystone Trench Co Business Card*

Looking for a professional, clean and crisp business card

I am in the underground utilities industry and am just looking for a really impressive business card. I would like our card to be white with our symbol crisp and clear with it protruding. I also have a business partner that will require his name and info on the card once the design is set. I would like to have our website info on the card which is;
http://keystonetrenchco.example/

Contact Information for Business Card

Website, contact name, number and email

```html
<!DOCTYPE html>
<html lang="en">
<head>
<meta charset="utf-8">
<title>Keystone Trench Co Business Card</title>
<link rel="stylesheet" href="https://fonts.googleapis.com/css2?family=Montserrat:wght@400;600&family=Saira+Condensed:wght@700&display=swap">
<style>
  :root {
    --bg: #1c1c1e;
    --card-white: #ffffff;
    --card-black: #0b0c0e;
    --tab-black: #050607;
    --slate: #363f4b;
    --pipe-slate: #2a323c;
    --ink: #2c323b;
    --ink-soft: #3a3f47;
    --accent-blue: #3a64b8;
    --mark-white: #ffffff;
  }
  * { box-sizing: border-box; margin: 0; padding: 0; }
  html, body { width: 1200px; height: 900px; overflow: hidden; }
  body {
    background: var(--bg);
    font-family: "Montserrat", sans-serif;
    position: relative;
  }
  .card {
    position: absolute;
    top: 100px;
    width: 400px;
    height: 700px;
    border-radius: 4px;
    overflow: hidden;
    box-shadow: 0 20px 40px rgba(0,0,0,.45);
  }
  .card--back { left: 170px; background: var(--card-black); }
  .card--front { left: 630px; background: var(--card-white); }

  .logo-tab {
    position: absolute;
    top: 0;
    right: 24px;
    width: 300px;
    height: 300px;
    border-radius: 0 0 150px 150px;
    display: flex;
    align-items: center;
    justify-content: center;
    gap: 10px;
    padding: 0 28px;
  }
  .card--back .logo-tab { background: var(--slate); }
  .card--front .logo-tab { background: var(--tab-black); }

  .brand-dot {
    flex: none;
    width: 16px;
    height: 16px;
    border-radius: 50%;
    background: var(--mark-white);
  }
  .brand-name {
    font-family: "Montserrat", sans-serif;
    font-weight: 600;
    font-size: 24px;
    line-height: 1.2;
    color: var(--mark-white);
    text-align: center;
  }

  .pipe-field {
    position: absolute;
    left: 0;
    right: 0;
    top: 300px;
    bottom: 0;
    background: linear-gradient(160deg, var(--pipe-slate) 0%, #161a20 55%, var(--card-black) 100%);
  }

  .contact-block {
    position: absolute;
    left: 40px;
    right: 40px;
    bottom: 70px;
    text-align: center;
    color: var(--ink);
  }
  .contact-name {
    font-family: "Saira Condensed", sans-serif;
    font-weight: 700;
    font-size: 34px;
    letter-spacing: 1px;
    text-transform: uppercase;
    color: var(--ink);
    margin-bottom: 14px;
  }
  .contact-rule {
    display: flex;
    align-items: center;
    gap: 12px;
    margin-bottom: 18px;
  }
  .contact-rule .line { flex: 1; height: 2px; background: var(--accent-blue); }
  .contact-rule svg { width: 18px; height: 18px; flex: none; }
  .contact-lines { font-size: 17px; line-height: 1.7; color: var(--ink-soft); letter-spacing: .3px; }
  .contact-lines .domain { color: var(--accent-blue); }
</style>
</head>
<body>
  <section class="card card--back" aria-label="Card back">
    <div class="logo-tab">
      <span class="brand-dot"></span>
      <span class="brand-name">Keystone Trench Co</span>
    </div>
    <div class="pipe-field" role="img" aria-label="Repeating pattern of dark slate flanged pipes"></div>
  </section>

  <section class="card card--front" aria-label="Card front">
    <div class="logo-tab">
      <span class="brand-dot"></span>
      <span class="brand-name">Keystone Trench Co</span>
    </div>

    <div class="contact-block">
      <p class="contact-name">Dale Okonski</p>
      <div class="contact-rule">
        <span class="line"></span>
        <svg viewBox="0 0 20 20" aria-hidden="true"><circle cx="10" cy="10" r="8.5" fill="none" stroke="#3a64b8" stroke-width="1.6"/><path d="M7 6.2c.6-.6 1.3-.3 1.6.3l.6 1.2c.2.4 0 .8-.3 1l-.5.4c.5 1.1 1.3 1.9 2.4 2.4l.4-.5c.3-.3.7-.4 1-.2l1.2.6c.6.3.8 1 .3 1.6-.8.9-2 .9-3.2.3-1.9-1-3.1-2.2-4-4-.5-1.2-.4-2.3.5-3.1z" fill="#3a64b8"/></svg>
        <svg viewBox="0 0 20 20" aria-hidden="true"><rect x="2.5" y="5" width="15" height="10.5" rx="1" fill="none" stroke="#3a64b8" stroke-width="1.6"/><path d="M3 5.6l7 5.4 7-5.4" fill="none" stroke="#3a64b8" stroke-width="1.6"/></svg>
        <svg viewBox="0 0 20 20" aria-hidden="true"><circle cx="10" cy="10" r="8" fill="#3a64b8"/><path d="M2 10h16M10 2c-3 3-3 13 0 16M10 2c3 3 3 13 0 16" fill="none" stroke="#fff" stroke-width="1.1"/></svg>
        <span class="line"></span>
      </div>
      <div class="contact-lines">
        <p>604-555-0182</p>
        <p>dale@keystonetrenchco.example</p>
        <p>www.<span class="domain">keystonetrenchco</span>.example</p>
      </div>
    </div>
  </section>
</body>
</html>
```